Brintel Works - Fast, Efficient and Gas Mainteance for Domestic, Commercial and Industrial clients

We are in the process of purchasing a new business and would like to get a new logo and business card.
Business is a gas maintenance business that also does new gas installations.
Has been established since 1988.
Services include:
Install all types of gas appliances & equipment inc. hot water units
Maintain / repair / replace all types of gas appliances & equipment

Target Market(s)

Domestic, Commercial and Industrial clients

Industry/Entity Type

Business

Contact Information for Business Card

admin@brintelworks.com.au
07 3918 4726
Brintel Works PTY LTD

Logo Text

Gas Fitting & Plumbing Maintenance Specialists

Font styles to use
Sans Serif

Requirements
Must have
• Logo
• Business name, contact number, email address, web address
• Domestic | Commercial | Industrial Est Since 1988
Nice to have
• Possibly a black card with a flame logo to one side
Should not have
• Spelling errors

```html
<!DOCTYPE html>
<html lang="en">
<head>
<meta charset="utf-8">
<title>Brintel Works – Business Card</title>
<link rel="stylesheet" href="https://fonts.googleapis.com/css2?family=Open+Sans:wght@400;700;800&display=swap">
<style>
  :root {
    --stage: #e9e6e3;
    --card-black: #000000;
    --flame-orange: #f47a28;
    --flame-red: #e8302a;
    --gold: #ffcf3a;
    --amber: #f9a21b;
    --white: #ffffff;
  }
  * { box-sizing: border-box; margin: 0; padding: 0; }
  html, body { width: 1200px; height: 900px; overflow: hidden; }
  body {
    position: relative;
    background: var(--stage);
    font-family: "Open Sans", Arial, sans-serif;
  }
  .card {
    position: absolute;
    background: var(--card-black);
    border-radius: 14px;
    overflow: hidden;
    box-shadow: 0 6px 18px rgba(0,0,0,.25);
  }
  /* Front card */
  .card-front { left: 78px; top: 35px; width: 588px; height: 362px; }
  .header-band {
    position: absolute; left: 0; top: 40px; width: 100%; height: 105px;
    background: linear-gradient(to bottom, var(--flame-orange), var(--flame-red));
  }
  .mark-circle {
    position: absolute; left: 34px; top: 7px; width: 156px; height: 156px;
    border-radius: 50%; background: var(--card-black);
  }
  .brand {
    position: absolute; text-align: center;
    font-weight: 800; color: var(--gold); line-height: 1;
  }
  .brand-name { font-size: 36px; letter-spacing: .2px; }
  .brand-suffix { font-size: 13px; letter-spacing: 2px; margin-top: 5px; font-weight: 800; }
  .card-front .brand { left: 218px; width: 340px; top: 67px; }
  .contact-list {
    position: absolute; left: 0; width: 100%; top: 197px;
    list-style: none; text-align: center; color: var(--white); font-size: 16px;
  }
  .contact-list li { height: 25px; line-height: 25px; }
  .contact-list svg { width: 11px; height: 11px; margin-right: 5px; vertical-align: -1px; }
  .address {
    position: absolute; left: 112px; width: 364px; top: 291px; text-align: center;
    color: var(--white); font-size: 15.5px;
  }
  /* Back card */
  .card-back { left: 389px; top: 506px; width: 565px; height: 350px; }
  .side-stripe {
    position: absolute; left: 40px; top: 0; width: 43px; height: 100%;
    background: linear-gradient(to bottom, var(--flame-orange), var(--flame-red));
  }
  .mark-dot {
    position: absolute; left: 233px; top: 66px; width: 130px; height: 130px;
    border-radius: 50%; background: var(--flame-red);
  }
  .card-back .brand { left: 120px; width: 355px; top: 215px; color: var(--amber); }
  .tagline {
    position: absolute; left: 110px; width: 375px; top: 280px;
    text-align: center; font-weight: 700; font-size: 15px; color: var(--amber);
  }
</style>
</head>
<body>
  <section class="card card-front" aria-label="Business card front">
    <div class="header-band"></div>
    <div class="mark-circle"></div>
    <div class="brand">
      <div class="brand-name">Brintel Works</div>
      <div class="brand-suffix">PTY LTD</div>
    </div>
    <ul class="contact-list">
      <li><svg viewBox="0 0 12 12"><path fill="#e8302a" d="M2.4 0.5 4.3 2.6 3.4 4.2c.8 1.7 2.5 3.4 4.3 4.3l1.6-.9 2.1 1.9-1.2 2C5.2 11.5.5 6.8.5 1.7z"/></svg>07 3918 4726</li>
      <li><svg viewBox="0 0 12 12"><rect x="0.5" y="2" width="11" height="8" fill="#e8302a"/><path d="M0.8 2.4 6 6.6l5.2-4.2" fill="none" stroke="#000" stroke-width="1"/></svg>admin@brintelworks.com.au</li>
      <li><svg viewBox="0 0 12 12"><g fill="none" stroke="#e8302a" stroke-width="1.6"><rect x="0.8" y="5" width="6" height="3.2" rx="1.6" transform="rotate(-45 3.8 6.6)"/><rect x="5.2" y="3.8" width="6" height="3.2" rx="1.6" transform="rotate(-45 8.2 5.4)"/></g></svg>www.brintelworks.com.au</li>
    </ul>
    <p class="address">12345, Address Goes Here Country Name, 123456</p>
  </section>

  <section class="card card-back" aria-label="Business card back">
    <div class="side-stripe"></div>
    <div class="mark-dot"></div>
    <div class="brand">
      <div class="brand-name">Brintel Works</div>
      <div class="brand-suffix">PTY LTD</div>
    </div>
    <p class="tagline">Domestic | Commercial | Industrial Est Since 1988</p>
  </section>
</body>
</html>
```